Glen Whitmore Professional Coaching

I would like a website with a mountain theme geared towards professional executives reaching higher peaks and goals. This is a 3 page website with brand essence information on the opening page, the coaching process on a second page and "about me" and lead capture form on a third page

Target Market(s)

C-Level audience, involved in tech, government, manufacturing, and transportation type of corporations

Coding

Coded - Design and coding required

Number of Pages Required

3 page

Font styles to use
Sans Serif

Colors
a7a7a7
1b1b1b
e8e8e8
3176b5
abd036
0355a3

Requirements
Must have
• Looking for a user friendly site that I can manage/update going forward. Must have:
• 1. "Is coaching right for you?" - page 1
• 2. "Our Process" page 2 - I will describe how we approach coaching
• 3. "Contact us" page 3 where I can capture contact information from potential clients
• 4. Clean and professional with more modern font
• 5. Links to personal social media sites
• 6. Ability to upload/download .pdf documents as resources
• 7. Ability to add on new pages in the future (such as a blog page)
Nice to have
• I want a place to store articles I write or use.
• LinkedIn or Twitter Feed
Should not have
• Not fluffy or too 'zen' like personal life coaches tend to present.

```html
<!DOCTYPE html>
<html lang="en">
<head>
<meta charset="utf-8">
<title>Glen Whitmore Professional Coaching</title>
<link href="https://fonts.googleapis.com/css2?family=Lato:wght@400;700;900&family=Great+Vibes&display=swap" rel="stylesheet">
<style>
:root{
  --teal:#1fa5c6;
  --navy:#0b2a55;
  --ink:#1b1b1b;
  --night:#23242f;
  --mist:#eef0ef;
  --grey:#a7a7a7;
  --text:#5e6266;
  --white:#ffffff;
}
*{margin:0;padding:0;box-sizing:border-box}
html,body{width:1200px;height:3000px;overflow:hidden}
body{position:relative;font-family:'Lato',sans-serif;color:var(--ink);background:var(--white)}
.abs{position:absolute}

/* hero */
.hero-backdrop{left:0;top:0;width:1200px;height:720px;
  background:linear-gradient(180deg,#0a2a58 0%,#1d4f86 22%,#8da4ba 48%,#d5dde2 70%,var(--mist) 100%)}
.site-nav{left:0;top:0;width:1200px;height:160px}
.brand{left:110px;top:56px;font-size:40px;font-weight:400;color:var(--white);letter-spacing:.5px}
.nav-links{left:497px;top:68px;display:flex;gap:0;font-size:17px;color:var(--white)}
.nav-links span{margin-right:44px}
.nav-divider{left:860px;top:62px;width:1px;height:32px;background:rgba(255,255,255,.4)}
.nav-call{left:880px;top:62px;display:flex;align-items:center;gap:14px;font-size:17px;font-weight:700;color:var(--white)}
.icon-dot{width:32px;height:32px;border-radius:50%;background:var(--teal);display:flex;align-items:center;justify-content:center}
.hero-title{left:184px;top:364px;width:832px;height:62px;background:var(--teal);color:var(--white);
  font-size:36px;font-weight:700;text-transform:uppercase;text-align:center;line-height:62px;letter-spacing:.3px}
.hero-sub{left:282px;top:434px;width:636px;height:56px;background:#eeeeee;color:#555;font-size:17px;text-align:center;line-height:56px}
.slider-dots{left:550px;top:594px;display:flex;gap:10px}
.slider-dots i{width:13px;height:13px;border-radius:50%;background:var(--white);display:block}
.slider-dots i.on{background:var(--teal)}

/* about */
.about-band{left:0;top:720px;width:1200px;height:566px;background:var(--mist)}
.portrait{left:0;top:680px;width:620px;height:606px;
  background:linear-gradient(180deg,#c9b6a6 0%,#a98c79 25%,#2a3b63 55%,#1d2b4d 100%);border-radius:280px 300px 0 0}
.ghost{font-weight:900;text-transform:uppercase;white-space:nowrap;line-height:1}
.about-ghost{left:704px;top:746px;font-size:74px;color:rgba(0,0,0,.06)}
.script{font-family:'Great Vibes',cursive;font-weight:400;line-height:1}
.about-title{left:664px;top:764px;font-size:54px;color:var(--ink)}
.rule{height:4px;width:48px;background:var(--teal)}
.about-rule{left:666px;top:842px}
.about-copy{left:666px;top:874px;width:440px;font-size:14.5px;line-height:39px;color:var(--text)}
.btn{height:54px;border-radius:27px;background:var(--teal);color:var(--white);font-size:14px;font-weight:700;
  text-transform:uppercase;display:flex;align-items:center;justify-content:center;gap:8px}
.about-btn{left:668px;top:1110px;width:184px}

/* process */
.process{left:0;top:1286px;width:1200px;height:770px;background:var(--night)}
.process-backdrop{left:0;top:1286px;width:1200px;height:770px;
  background:radial-gradient(ellipse at 70% 70%,rgba(255,255,255,.07),rgba(255,255,255,0) 60%)}
.process-ghost{left:0;top:1424px;width:1200px;text-align:center;font-size:74px;color:rgba(255,255,255,.05)}
.process-title{left:0;top:1440px;width:1200px;text-align:center;font-size:54px;color:var(--white)}
.process-rule{left:576px;top:1520px}
.step{width:260px;text-align:center;color:var(--white)}
.step-icon{width:132px;height:132px;border-radius:50%;background:var(--teal);margin:0 auto;display:flex;align-items:center;justify-content:center}
.step p{margin-top:30px;font-size:13px;line-height:23px}
.step b{display:block;margin-top:22px;font-size:46px;font-weight:700}
.step-1{left:84px;top:1610px}
.step-2{left:470px;top:1610px}
.step-3{left:856px;top:1610px}
.flow{left:0;top:1600px}

/* contact */
.contact-backdrop{left:0;top:2200px;width:1200px;height:660px;
  background:linear-gradient(180deg,rgba(255,255,255,0) 0%,#b9c0c6 25%,#8e979f 50%,#d8dde1 80%,#ffffff 100%);
  clip-path:polygon(0 40%,25% 28%,45% 10%,55% 0,68% 12%,80% 22%,100% 38%,100% 100%,0 100%)}
.contact-ghost{left:112px;top:2192px;font-size:74px;color:rgba(0,0,0,.06)}
.contact-title{left:112px;top:2210px;font-size:54px;color:var(--ink)}
.contact-rule{left:114px;top:2288px}
.field{background:var(--white);height:56px;font-size:13px;color:#555;padding:18px 26px;box-shadow:0 2px 8px rgba(0,0,0,.08)}
.f-name{left:114px;top:2372px;width:396px}
.f-email{left:524px;top:2372px;width:396px}
.f-address{left:114px;top:2454px;width:396px}
.f-phone{left:524px;top:2454px;width:396px}
.f-message{left:114px;top:2536px;width:806px;height:134px}
.submit-btn{left:114px;top:2736px;width:208px}

/* footer */
.foot-item{top:2852px;display:flex;align-items:center;gap:18px;font-size:14px;color:#444}
.foot-icon{width:46px;height:46px;border-radius:50%;border:1.5px solid #d0d4d7;display:flex;align-items:center;justify-content:center;background:var(--white)}
.foot-call{left:112px}
.foot-mail{left:376px}
.stay{left:758px;top:2860px;font-size:24px;font-weight:700;color:var(--ink)}
.socials{left:952px;top:2856px;display:flex;gap:12px}
.socials i{width:38px;height:38px;border-radius:50%;border:1.5px solid #d0d4d7;display:block}
.legal{left:112px;top:2928px;font-size:13px;color:#444}
</style>
</head>
<body>

<div class="abs hero-backdrop" role="img" aria-label="Snow-capped mountain peak against a deep blue sky"></div>

<header class="abs site-nav">
  <div class="abs brand">Glen Whitmore</div>
  <nav class="abs nav-links"><span>Home</span><span>Coaching process</span><span>About me</span></nav>
  <div class="abs nav-divider"></div>
  <div class="abs nav-call">
    <span class="icon-dot"><svg width="16" height="16" viewBox="0 0 24 24"><path fill="#fff" d="M6.6 10.8a15 15 0 0 0 6.6 6.6l2.2-2.2c.3-.3.7-.4 1-.2 1.1.4 2.3.6 3.6.6.6 0 1 .4 1 1V20c0 .6-.4 1-1 1A17 17 0 0 1 3 4c0-.6.4-1 1-1h3.5c.6 0 1 .4 1 1 0 1.3.2 2.5.6 3.6.1.3 0 .7-.2 1z"/></svg></span>
    CALL : 1 555 014 2290
  </div>
</header>

<h1 class="abs hero-title">Glen Whitmore Professional Coaching</h1>
<div class="abs hero-sub">Sed ut perspiciatis unde omnis iste natus error sit voluptatem accusantium</div>
<div class="abs slider-dots"><i></i><i></i><i class="on"></i><i></i><i></i></div>

<section>
  <div class="abs about-band"></div>
  <div class="abs portrait" role="img" aria-label="Portrait of the coach in a navy blazer and checked shirt"></div>
  <div class="abs ghost about-ghost">About me</div>
  <h2 class="abs script about-title">About me</h2>
  <div class="abs rule about-rule"></div>
  <p class="abs about-copy">Sed ut perspiciatis unde omnis iste natus error sit voluptatem accusantium doloremque laudantiuotam rem aperique ipsa quae ab illo inventore veritatis et quitae dicta sunt explicabo.<br>Nemo enim ipsam voluptatem quia voluptas sit aspernatur aut odit aut fugit, sed quiagoluptatem sequi nesciunt.</p>
  <div class="abs btn about-btn">Read more
    <svg width="14" height="14" viewBox="0 0 16 16"><circle cx="8" cy="8" r="8" fill="#fff"/><path d="M6.5 4.5 10 8l-3.5 3.5" stroke="#1fa5c6" stroke-width="2" fill="none"/></svg>
  </div>
</section>

<section>
  <div class="abs process"></div>
  <div class="abs process-backdrop" role="img" aria-label="Faint mountain range in the dark background"></div>
  <div class="abs ghost process-ghost">Coaching process</div>
  <h2 class="abs script process-title">Coaching Process</h2>
  <div class="abs rule process-rule"></div>

  <svg class="abs flow" width="1200" height="160" viewBox="0 0 1200 160">
    <defs><marker id="arrowhead" markerWidth="10" markerHeight="10" refX="8" refY="5" orient="auto"><path d="M0 0 10 5 0 10z" fill="#fff"/></marker></defs>
    <path d="M310 68 Q400 10 505 60" stroke="#fff" stroke-width="2" stroke-dasharray="5 5" fill="none" marker-end="url(#arrowhead)"/>
    <path d="M695 92 Q800 140 895 66" stroke="#fff" stroke-width="2" stroke-dasharray="5 5" fill="none" marker-end="url(#arrowhead)"/>
  </svg>

  <div class="abs step step-1">
    <div class="step-icon"><svg width="54" height="62" viewBox="0 0 54 62"><path d="M4 2h32l14 14v44H4z" fill="#fff"/><path d="M36 2v14h14" fill="#d5eef5"/><path d="M13 28h28M13 36h28M13 44h28M13 20h14" stroke="#1fa5c6" stroke-width="3"/></svg></div>
    <p>Sed ut perspiciatis unde omnis iste natus error sit voluptatem accusantium doloremque laudantium</p>
    <b>01</b>
  </div>
  <div class="abs step step-2">
    <div class="step-icon"><svg width="64" height="50" viewBox="0 0 64 50"><g fill="#fff"><circle cx="32" cy="11" r="9"/><circle cx="13" cy="16" r="7"/><circle cx="51" cy="16" r="7"/><path d="M18 48c0-12 6-18 14-18s14 6 14 18z"/><path d="M0 46c0-10 5-15 13-15 3 0 5 1 7 2-3 4-4 8-4 13z"/><path d="M64 46c0-10-5-15-13-15-3 0-5 1-7 2 3 4 4 8 4 13z"/></g></svg></div>
    <p>Sed ut perspiciatis unde omnis iste natus error sit voluptatem accusantium doloremque laudantium</p>
    <b>02</b>
  </div>
  <div class="abs step step-3">
    <div class="step-icon"><svg width="40" height="62" viewBox="0 0 40 62"><path d="M20 2a18 18 0 0 0-11 32c2 2 3 5 3 8v4h16v-4c0-3 1-6 3-8A18 18 0 0 0 20 2z" fill="#fff"/><path d="M14 50h12M15 56h10" stroke="#fff" stroke-width="4" stroke-linecap="round"/><path d="M16 40V26l4 4 4-4v14" stroke="#1fa5c6" stroke-width="2.5" fill="none"/></svg></div>
    <p>Sed ut perspiciatis unde omnis iste natus error sit voluptatem accusantium doloremque laudantium</p>
    <b>03</b>
  </div>
</section>

<section>
  <div class="abs contact-backdrop" role="img" aria-label="Snowy mountain peaks fading into mist"></div>
  <div class="abs ghost contact-ghost">Get in touch</div>
  <h2 class="abs script contact-title">Get in Touch</h2>
  <div class="abs rule contact-rule"></div>

  <div class="abs field f-name">Enter Name</div>
  <div class="abs field f-email">Enter Email</div>
  <div class="abs field f-address">Address</div>
  <div class="abs field f-phone">Phone</div>
  <div class="abs field f-message">Message</div>
  <div class="abs btn submit-btn">Submit message
    <svg width="14" height="14" viewBox="0 0 16 16"><circle cx="8" cy="8" r="8" fill="#fff"/><path d="M6.5 4.5 10 8l-3.5 3.5" stroke="#1fa5c6" stroke-width="2" fill="none"/></svg>
  </div>
</section>

<footer>
  <div class="abs foot-item foot-call">
    <span class="foot-icon"><svg width="18" height="18" viewBox="0 0 24 24"><path fill="#1fa5c6" d="M6.6 10.8a15 15 0 0 0 6.6 6.6l2.2-2.2c.3-.3.7-.4 1-.2 1.1.4 2.3.6 3.6.6.6 0 1 .4 1 1V20c0 .6-.4 1-1 1A17 17 0 0 1 3 4c0-.6.4-1 1-1h3.5c.6 0 1 .4 1 1 0 1.3.2 2.5.6 3.6.1.3 0 .7-.2 1z"/></svg></span>
    CALL US : 1 555 014 2290
  </div>
  <div class="abs foot-item foot-mail">
    <span class="foot-icon"><svg width="20" height="16" viewBox="0 0 20 16"><rect x="0" y="0" width="20" height="16" rx="2" fill="#1fa5c6"/><path d="M1 2l9 7 9-7" stroke="#fff" stroke-width="1.8" fill="none"/></svg></span>
    EMAIL US : hello@whitmorecoaching.com
  </div>
  <div class="abs stay">Stay connected</div>
  <div class="abs socials" aria-label="Social media links"><i></i><i></i><i></i></div>
  <div class="abs legal">2019 © Whitmore Coaching. All Rights Reserved &nbsp;|&nbsp; Privacy Policy</div>
</footer>

</body>
</html>
```